Magazine Template for National Charity

We need a magazine design for an Australian youth charity called Rhythm Crews Lifting FUtures (RCLF). We engage young people through street culture music, dance and mentoring programs, and help them to turn their lives around. Our charity's vision is to see every young person have someone who believes in them and the opportunity to live their potential.

The design should have places for images of our young people during programs(we've only provided a few for you), room for quotes from young people and supporters etc, and each double spread could be a snapshot of a different program.

We will need a design template that will allow us to add all the contents for the magazine, including a contents page, report from our Chairman (1 page), letter from CEO (1 page), and following achievements of our programs including 1. RCLF Camps (2 x double spread, total 4 pages), 2. Groove Labs (2 x double spread, total 4 pages) and 3. Mentoring (2 x double spread, total 4 pages). An audited financial report of 4 pages will be copied in after our program reports, and on the back of the magazine, we'll need space for all our supporter logos. I'd also like to include a short story or case-study about young people's transformation on each program page.

We need something that's got a bit of a street edge, to keep our youthful brand, but helps us to highlight our excellence as an innovative and cutting edge charity. The final design should be emotional, eye-catching, reflective of our creative spark, and inspiring. We currently have a brand that uses a fair bit of black & white with highlights of colour, however I dont want this to limit your creativity. We use a font called Octin Spraypaint Free for our logos and program names.

We would like to present our annual report as a magazine so that it is something that people will want to pick up and look at.

Target Market(s)

This is for general public and supporters, however we'd like to use our brand instead of a professional style for this report

Industry/Entity Type

Financial

Requirements
Must have
• See notes in task description - thank you!

We will give you a few images to use as a guide however we'd love to be able to play around with the images once we have a template (we'll add different ones and change pictures around to suit the program pages). We're providing these images so that you can get a feel for our culture and be inspired to put together the template, dont worry if you use the same photos more than once on the different pages to show as an example.
Nice to have
• We already have our charity logo, however we'd love to call this RCLF Mag, RCLF Magazine or Newest RCLF Rhythmania. We'd like it to replicate a real magazine, with colour and lots of interesting sections for information & stories, rather than a boring traditional annual report template.
Should not have
• We want this magazine to stand out, and we dont want a half-hearted charity design or a polished corporate style magazine.

We want to remain bold and contemporary, and on the commercial side with a street edge - have lots of fun & thank you so much - we're very excited!

```html
<!DOCTYPE html>
<html lang="en">
<head>
<meta charset="utf-8">
<title>RCLF Magazine – Stories from the RCLF Camps</title>
<link rel="stylesheet" href="https://fonts.googleapis.com/css2?family=Big+Shoulders+Stencil+Display:wght@500;700&family=Arimo:wght@400;700&display=swap">
<style>
  :root {
    --red: #e8141b;
    --white: #ffffff;
    --ink: #1a1a1a;
    --photo-mono: #8d8d8d;
    --photo-light: #d9d9d9;
    --photo-warm: #b35a4a;
    --photo-sky: #9fb6c8;
  }
  * { margin: 0; padding: 0; box-sizing: border-box; }
  html, body { width: 1200px; height: 855px; overflow: hidden; background: var(--red); }
  .spread {
    position: relative; width: 1200px; height: 855px; overflow: hidden;
    background: var(--red); color: var(--white);
    font-family: "Arimo", Arial, sans-serif;
  }
  .stencil { font-family: "Big Shoulders Stencil Display", "Arimo", sans-serif; font-weight: 500; }

  .section-badge {
    position: absolute; left: 47px; top: 50px; width: 117px; height: 117px;
    border-radius: 50%; background: var(--white); color: var(--red);
    display: flex; align-items: center; justify-content: center; text-align: center;
    font-size: 17px; line-height: 1.15; letter-spacing: 0.5px;
  }

  .pull-quote { position: absolute; text-transform: uppercase; white-space: nowrap; }
  .pull-quote--left { left: 46px; top: 168px; font-size: 62px; line-height: 73px; letter-spacing: 3px; }
  .pull-quote--right { right: 52px; top: 312px; font-size: 38px; line-height: 42px; letter-spacing: 2px; text-align: right; }

  .photo { position: absolute; border-radius: 50%; }
  .photo--camper { left: 47px; top: 356px; width: 292px; height: 292px;
    background: radial-gradient(circle at 40% 45%, var(--photo-light), var(--photo-mono) 70%, #4a4a4a); }
  .photo--film { left: 634px; top: 48px; width: 134px; height: 134px;
    background: linear-gradient(170deg, var(--photo-light) 0%, #555 50%, var(--photo-sky) 100%); }
  .photo--dance { left: 923px; top: 491px; width: 222px; height: 222px;
    background: linear-gradient(160deg, var(--photo-light) 0%, var(--photo-warm) 45%, #3a2a25 70%, var(--photo-sky) 100%); }

  .story { position: absolute; font-size: 10.5px; line-height: 14px; }
  .story h3 { font-size: 10.5px; font-weight: 700; }
  .story p { margin-bottom: 14px; }
  .story--camp { left: 367px; top: 424px; width: 215px; }
  .story--film { left: 815px; top: 103px; width: 300px; }
  .story--dance { left: 660px; top: 535px; width: 250px; text-align: right; }

  .brand-tab {
    position: absolute; right: 52px; top: 0; height: 48px; padding: 6px 8px 0 8px;
    background: var(--white); color: var(--ink); border-radius: 0 0 8px 8px;
    display: flex; gap: 5px; align-items: flex-start;
  }
  .brand-tab__mark { width: 10px; height: 10px; background: var(--red); margin-top: 4px; }
  .brand-tab__name { font-size: 18px; line-height: 18px; text-transform: uppercase; letter-spacing: 0.5px; }

  .folio {
    position: absolute; bottom: 0; width: 22px; height: 38px;
    background: var(--white); color: var(--red); border-radius: 6px 6px 0 0;
    font-weight: 700; font-size: 14px; text-align: center; padding-top: 11px;
  }
  .folio--left { left: 46px; }
  .folio--right { right: 52px; }
  .footer-line { position: absolute; bottom: 18px; font-size: 10.5px; }
  .footer-line--left { left: 78px; }
  .footer-line--right { right: 82px; }
</style>
</head>
<body>
<main class="spread">

  <div class="section-badge stencil">STORIES<br>FROM THE<br>RCLF CAMPS</div>

  <blockquote class="pull-quote pull-quote--left stencil">“Ak dedef as<br>pajed tofdu”</blockquote>

  <div class="photo photo--camper" role="img" aria-label="Black and white photo of a smiling young camper in a striped top"></div>

  <article class="story story--camp">
    <h3>HEADING</h3>
    <p>Camp week opened with a drum circle on the lawn, and by lunch every crew had written its first rhyme together while mentors kept the beat going.</p>
    <p>Nobody was left on the edge. Older campers showed the new faces how to hold a mic and trust their voice.</p>
    <p>By the final night the hall was full of parents, friends and staff cheering a showcase built from scratch in just five days. Many said it felt like the start of something bigger, a place where they finally belonged and could dream out loud.</p>
    <p>We keep in touch after camp, so every young person has someone to call when things get hard.</p>
  </article>

  <div class="brand-tab">
    <span class="brand-tab__mark"></span>
    <span class="brand-tab__name stencil">Rhythm Crews<br>Lifting Futures</span>
  </div>

  <div class="photo photo--film" role="img" aria-label="Photo of two young people filming with a video camera beside a graffiti wall"></div>

  <article class="story story--film">
    <h3>HEADING</h3>
    <p>Filming the crews on day two gave young people a chance to tell their own stories, behind the lens and in front of it.</p>
    <p>Each clip was planned, shot and cut by the campers, with mentors on hand for tips and support.</p>
    <p>The finished reels now play at school visits, proof of what teamwork and a little belief can do.</p>
  </article>

  <blockquote class="pull-quote pull-quote--right stencil">“Ak dedef eaaf pajed tofdu<br>dfjf jdfdshjf jadfkhjhfj<br>ajfhjdfkjhdlkh djfhdlhf”</blockquote>

  <article class="story story--dance">
    <h3>HEADING</h3>
    <p>Dance workshops ran every afternoon, mixing breaking, krump and freestyle with plenty of laughs along the way.</p>
    <p>Young people who arrived shy were leading their own routines by the end of the week, cheered on by the crew.</p>
    <p>Those moments of pride stay with them long after camp, building the confidence to chase new goals back home.</p>
  </article>

  <div class="photo photo--dance" role="img" aria-label="Photo of young dancers performing in front of a colourful mural"></div>

  <div class="folio folio--left">6</div>
  <div class="footer-line footer-line--left">live your full potential</div>
  <div class="footer-line footer-line--right">www.rclf.org.au</div>
  <div class="folio folio--right">7</div>

</main>
</body>
</html>
```